BRIGHT RIVER POWER.

I'd like my business logo.
contact name: Dennis Halvorsen
phone:0438759164
email: info@brightriverpower.net.au
website: www.brightriverpower.net.au

services:
solar
battery storage
LED lighting
energy saving solutions
general electrical
I'd like the design to look professional

Target Market(s)

Everyone

Industry/Entity Type

Business

Contact Information for Business Card

as described above

Requirements
Must have
• Id like the colours and the design to work well with my logo.

```html
<!DOCTYPE html>
<html lang="en">
<head>
<meta charset="utf-8">
<title>Bright River Power – Business Card</title>
<link href="https://fonts.googleapis.com/css2?family=Source+Sans+3:wght@400;600;700&display=swap" rel="stylesheet">
<style>
  :root {
    --bg: #e9e6e1;
    --orange-light: #fbb040;
    --orange: #f7941d;
    --orange-deep: #ef7d14;
    --green-light: #9fd047;
    --green: #6cb33f;
    --green-deep: #3f9a2d;
    --white: #ffffff;
    --brand-green: #5fae3a;
    --sun: #f7a21b;
  }
  * { margin: 0; padding: 0; box-sizing: border-box; }
  html, body { width: 1200px; height: 843px; overflow: hidden; }
  body {
    background: var(--bg);
    font-family: "Source Sans 3", "Myriad Pro", Arial, sans-serif;
    position: relative;
  }
  .card {
    position: absolute;
    top: 272px;
    width: 520px;
    height: 300px;
    border-radius: 22px;
    overflow: hidden;
    box-shadow: 0 10px 28px rgba(0,0,0,0.18);
  }
  .card--front {
    left: 50px;
    background: radial-gradient(ellipse at 45% 30%, var(--orange-light) 0%, var(--orange) 55%, var(--orange-deep) 100%);
    color: var(--white);
  }
  .card--back { left: 630px; background: var(--white); }
  .brand {
    display: flex;
    align-items: center;
    justify-content: center;
    gap: 12px;
    font-weight: 700;
    letter-spacing: 0.5px;
  }
  .brand__dot { width: 30px; height: 30px; border-radius: 50%; flex: none; }
  .card--front .brand { position: absolute; left: 0; right: 0; top: 104px; font-size: 34px; color: var(--white); }
  .card--front .brand__dot { background: var(--white); }
  .services {
    position: absolute; left: 0; right: 0; top: 196px;
    text-align: center; font-size: 15px; letter-spacing: 0.6px;
  }
  .card--back .brand { position: absolute; left: 0; right: 0; top: 42px; font-size: 30px; color: var(--brand-green); }
  .card--back .brand__dot { background: var(--sun); }
  .wave { position: absolute; inset: 0; width: 100%; height: 100%; }
  .holder {
    position: absolute; left: 34px; top: 172px;
    color: var(--white); font-weight: 700; font-size: 20px; letter-spacing: 0.3px;
  }
  .contacts {
    position: absolute; right: 28px; top: 212px;
    list-style: none; color: var(--white); font-size: 15px; text-align: right;
  }
  .contacts li { display: flex; align-items: center; justify-content: flex-end; gap: 8px; height: 22px; }
  .contacts svg { width: 14px; height: 14px; fill: var(--white); flex: none; }
</style>
</head>
<body>
  <section class="card card--front" aria-label="Card front">
    <div class="brand"><span class="brand__dot"></span><span>BRIGHT RIVER POWER</span></div>
    <p class="services">Solar • Battery Storage • LED Lighting</p>
  </section>

  <section class="card card--back" aria-label="Card back">
    <svg class="wave" viewBox="0 0 520 300" preserveAspectRatio="none" aria-hidden="true">
      <defs>
        <linearGradient id="greenFill" x1="0" y1="0" x2="1" y2="1">
          <stop offset="0" stop-color="var(--green-light)"/>
          <stop offset="0.55" stop-color="var(--green)"/>
          <stop offset="1" stop-color="var(--green-deep)"/>
        </linearGradient>
      </defs>
      <path d="M0 128 C150 108 330 128 520 176 L520 300 L0 300 Z" fill="url(#greenFill)"/>
      <path d="M0 128 C150 108 330 128 520 176 L520 196 C330 150 160 138 0 158 Z" fill="#ffffff" opacity="0.18"/>
    </svg>
    <div class="brand"><span class="brand__dot"></span><span>BRIGHT RIVER POWER</span></div>
    <p class="holder">Dennis Halvorsen</p>
    <ul class="contacts">
      <li>0438759164
        <svg viewBox="0 0 24 24"><path d="M6.6 10.8a15.1 15.1 0 0 0 6.6 6.6l2.2-2.2c.3-.3.7-.4 1-.2 1.1.4 2.3.6 3.6.6.6 0 1 .4 1 1V20c0 .6-.4 1-1 1A17 17 0 0 1 3 4c0-.6.4-1 1-1h3.5c.6 0 1 .4 1 1 0 1.3.2 2.5.6 3.6.1.3 0 .7-.2 1z"/></svg>
      </li>
      <li>info@brightriverpower.net.au
        <svg viewBox="0 0 24 24"><path d="M2 5h20v14H2z M2 5l10 8 10-8" fill="none" stroke="#fff" stroke-width="2"/></svg>
      </li>
      <li>brightriverpower.net.au
        <svg viewBox="0 0 24 24"><circle cx="12" cy="12" r="9" fill="none" stroke="#fff" stroke-width="2"/><path d="M3 12h18M12 3c3 3 3 15 0 18M12 3c-3 3-3 15 0 18" fill="none" stroke="#fff" stroke-width="1.6"/></svg>
      </li>
    </ul>
  </section>
</body>
</html>
```